Family Owned and Operated Spray Foam Insulation Company needs a business card design

We're a new company based in the heart of Texas (Fort Worth). We spray foam insulation into residential houses, commercial buildings, metal buildings, etc. Spray foam insulation provides a huge reduction in energy/costs so that is what drives our market. We like the primary colors but are open to suggestions and are coming to the experts for some creativity. I'm attaching a picture of shirt mock up we have with KBL on the front to show what we were leaning towards as well as some business cards that I find striking and memorable. I'm looking for a card that is clean and professional with a bit of edge. Note: My computer won't pull up the color samples below for me to choose so it's in your hands.

Target Market(s)

Professional custom home builders, construction industry, home owners

Industry/Entity Type

Residential

Contact Information for Business Card

Name: Martin Kestrel (no title) Phone #: 817-555-0148, address: 4087 larkspur ave fort worth tx 76110, email: martin@kblinsulation.example, website: kblinsulation.example

Requirements
Must have
• We want the words KBL and Kestrel Spray Foam Insulation showcased on the card but hopefully on opposite sides
Should not have
• Any type of spray foam gun or splatter clip art

```html
<!DOCTYPE html>
<html lang="en">
<head>
<meta charset="utf-8">
<title>Kestrel Spray Foam Insulation – Business Card</title>
<link href="https://fonts.googleapis.com/css2?family=Cinzel:wght@400&family=Roboto+Condensed:wght@700&family=Roboto:wght@400&display=swap" rel="stylesheet">
<style>
  :root {
    --stage: #e9e6e1;
    --card-white: #ffffff;
    --brand-blue: #3a63c4;
    --brand-blue-deep: #2a44a8;
    --brand-blue-light: #4d7ad6;
    --brand-red: #e8353b;
    --rule: #9aa7c9;
    --text-white: #ffffff;
  }
  * { box-sizing: border-box; margin: 0; padding: 0; }
  html, body { width: 1200px; height: 885px; overflow: hidden; }
  body {
    background: var(--stage);
    display: flex;
    flex-direction: column;
    align-items: center;
    justify-content: center;
    gap: 29px;
  }
  .card {
    width: 700px;
    height: 400px;
    position: relative;
    overflow: hidden;
    box-shadow: 0 6px 18px rgba(0,0,0,0.18);
  }

  /* Front */
  .card--front { background: var(--card-white); }
  .front__company {
    position: absolute;
    left: 48px;
    top: 92px;
    width: 330px;
    text-align: center;
    font-family: "Cinzel", serif;
    font-size: 31px;
    line-height: 1.2;
    color: var(--brand-blue);
    letter-spacing: 1px;
  }
  .front__mark {
    position: absolute;
    right: 48px;
    top: 46px;
    font-family: "Roboto Condensed", sans-serif;
    font-weight: 700;
    font-size: 132px;
    line-height: 1;
    color: var(--brand-blue);
    letter-spacing: 2px;
  }
  .front__contacts {
    position: absolute;
    left: 40px;
    right: 40px;
    bottom: 44px;
    display: flex;
    align-items: center;
    font-family: "Roboto", sans-serif;
    font-size: 17px;
    line-height: 1.3;
    color: var(--brand-blue);
  }
  .contact-group { padding: 0 16px; }
  .contact-group:first-child { padding-left: 0; }
  .contact-group + .contact-group { border-left: 1px solid var(--rule); }
  .contact-name {
    font-family: "Roboto Condensed", sans-serif;
    font-weight: 700;
    font-size: 22px;
    color: var(--brand-red);
  }

  /* Back */
  .card--back {
    background: radial-gradient(ellipse at 40% 45%, var(--brand-blue-light) 0%, var(--brand-blue) 45%, var(--brand-blue-deep) 100%);
  }
  .back__watermark {
    position: absolute;
    left: 50%;
    top: 50%;
    transform: translate(-50%, -52%);
    font-family: "Roboto Condensed", sans-serif;
    font-weight: 700;
    font-size: 360px;
    line-height: 1;
    color: rgba(255,255,255,0.07);
    white-space: nowrap;
  }
  .back__mark {
    position: absolute;
    left: 0; right: 0;
    top: 88px;
    text-align: center;
    font-family: "Roboto Condensed", sans-serif;
    font-weight: 700;
    font-size: 150px;
    line-height: 1;
    color: var(--text-white);
    letter-spacing: 4px;
  }
  .back__company {
    position: absolute;
    left: 0; right: 0;
    top: 258px;
    text-align: center;
    font-family: "Roboto Condensed", sans-serif;
    font-weight: 700;
    font-size: 30px;
    color: var(--text-white);
  }
</style>
</head>
<body>
  <section class="card card--front" aria-label="Card front">
    <h1 class="front__company">Kestrel Spray Foam<br>Insulation</h1>
    <div class="front__mark">KBL</div>
    <div class="front__contacts">
      <div class="contact-group">
        <div class="contact-name">Martin Kestrel</div>
        <div>817-555-0148</div>
      </div>
      <div class="contact-group">
        <div>martin@kblinsulation.example</div>
        <div>kblinsulation.example</div>
      </div>
      <div class="contact-group">
        <div>4087 larkspur ave</div>
        <div>fort worth tx 76110</div>
      </div>
    </div>
  </section>

  <section class="card card--back" aria-label="Card back">
    <div class="back__watermark" aria-hidden="true">KBL</div>
    <div class="back__mark">KBL</div>
    <div class="back__company">Kestrel Spray Foam Insulation</div>
  </section>
</body>
</html>
```